Create a Wordpress Design (Dorrel)

We need a wordpress design for an established auction and real estate company based in Tennessee. The winning design will incorporate a professional color scheme with company logo in a clean layout. The design needs to consider that this will be developed on a responsive theme. Colors are those that will highlight the logo.
Updates

This client, an older gentleman, wants the site to mimic http://www.quillfordbidhouse.example/. If you can adjust you designs with this site in mind - perhaps 3 columns, less color etc. We are trying to get him a concept that he likes and he keeps mentioning this site. Do not copy this site, but keep it in mind while re-doing the concept. Thanks, - auction services -

Industry/Entity Type

Real Estate

Font styles to use
Sans Serif

Colors

Designer to choose colors to be used in the design.

Requirements
Must have
• - Navigation: 1) Home - with auctions as content as seen at http://brenwickgavel.example/ 2) Properties for Sale 3) Auctions 4) Sell Your Property 5) Community Info 6) About Us 7) Contact Us

Color will be those that highlight logo in a professional creative way. Site tagline: "Our Signs are Everywhere". Site will have a slideshow - please use stock real estate image for the initial photo.

Widgets: 1) social media (FB twitter, linked In, Youtube, RSS) 2) News & Events blog, 3) testimonials 4) featured Property widget.

Footer will have contact info (below) smaller company logo, and the association logos attached, and contact info:
Phone: (615) 555-0178
Contacts: Marion Teague-Hollis
Email: marketing@kenwoodorrel.example
Address: 22-C Elmfield Court W, Murfreesboro, TN 37199

Nice to have
• use and styling of a dropdown menu: Under AUCTIONS, 1) Upcoming 2) Past

```html
<!DOCTYPE html>
<html lang="en">
<head>
<meta charset="utf-8">
<title>Dorrel Commercial Realtors, Auctioneers LLC</title>
<link href="https://fonts.googleapis.com/css2?family=Arimo:ital,wght@0,400;0,700;1,400&family=Open+Sans:wght@400;600;700&display=swap" rel="stylesheet">
<style>
:root{
  --red:#c8101f;
  --red-dark:#a50c18;
  --navy:#1f3f86;
  --ink:#222;
  --muted:#444;
  --panel:#eeeeee;
  --panel-line:#c9c9c9;
  --backdrop:#a9a9a9;
  --footer:#333;
  --btn:#4a4a4a;
}
*{box-sizing:border-box;margin:0;padding:0}
html,body{width:710px;height:1200px;overflow:hidden;background:var(--backdrop)}
body{font-family:Arimo,Arial,sans-serif;color:var(--ink)}
.stage{position:absolute;left:0;top:0;width:888px;height:1500px;transform:scale(.8);transform-origin:0 0}
.page{position:absolute;left:74px;top:0;width:740px;height:1500px;background:#fff}
.abs{position:absolute}

/* header */
.brand{left:10px;top:14px;width:180px;height:80px;display:flex;align-items:center;gap:10px}
.brand-dot{width:18px;height:18px;border-radius:50%;background:var(--red);flex:none}
.brand-name{font-family:"Open Sans",sans-serif;font-weight:700;font-size:21px;color:var(--red);line-height:1.1}
.tagline{left:239px;top:42px;font-family:"Open Sans",sans-serif;font-size:23px;color:#222}
.social{left:564px;top:46px;display:flex;gap:10px}
.social span{width:23px;height:23px;border-radius:50%;background:#8a8f99;display:block}

/* nav */
.nav{left:0;top:110px;width:740px;height:41px;background:linear-gradient(#e9e9e9,#cfcfcf);display:flex;border-bottom:1px solid #bdbdbd}
.nav a{display:flex;align-items:center;justify-content:center;font-size:11px;font-weight:700;color:#222;text-decoration:none;border-right:1px solid #b7b7b7;height:100%}
.nav a.active{background:var(--red);color:#fff}
.dropdown{left:208px;top:151px;width:146px}
.dropdown a{display:block;height:26px;line-height:26px;padding-left:7px;font-size:11.5px;text-decoration:none;font-family:"Open Sans",sans-serif}
.dropdown .up{background:#5b5b5b;color:#eee}
.dropdown .past{background:#c8c8c8;color:#333;height:30px;line-height:30px}

.hero{left:0;top:151px;width:740px;height:292px;background:linear-gradient(180deg,#9cc1e6 0%,#cfe0ee 30%,#a3432f 45%,#8a3528 62%,#6f8a46 80%,#58762f 100%)}

/* welcome */
.welcome{left:16px;top:468px;width:460px}
.welcome h1{font-weight:400;font-size:17px;color:var(--navy);margin-bottom:8px}
.welcome p{font-size:9.5px;line-height:15px;color:var(--muted)}

/* auction cards */
.card{left:15px;width:455px;height:231px;background:var(--panel);border:1px solid var(--panel-line)}
.card-head{position:absolute;left:-1px;top:-1px;width:455px;height:34px;background:var(--red);border-radius:4px 4px 0 0;color:#fff;font-weight:700;font-size:12px;letter-spacing:.3px;padding:11px 0 0 16px}
.card-photo{left:26px;top:44px;width:118px;height:78px;background:linear-gradient(#b9c7d4 0%,#c9d3da 35%,#7b9250 45%,#5f7a3c 100%);box-shadow:2px 2px 3px rgba(0,0,0,.35)}
.card-btn{left:53px;width:77px;height:24px;background:var(--btn);border-radius:3px;color:#eee;font-size:10px;display:flex;align-items:center;gap:7px;padding-left:9px}
.card-btn i{width:14px;height:12px;background:#b9d1e6;border-radius:2px;display:block}
.card-date{left:164px;top:51px;font-weight:700;font-size:12.5px;letter-spacing:.8px}
.card-desc{left:165px;top:72px;font-size:10px;line-height:14px;width:250px}
.bid{left:239px;top:100px;width:183px;height:24px;background:#fff;border:1px solid #ccc;box-shadow:1px 2px 3px rgba(0,0,0,.25);border-radius:2px;font-size:10px;display:flex;align-items:center;gap:8px;padding-left:10px}
.bid svg{flex:none}
.card-info{left:166px;top:130px;font-size:10px;line-height:14.5px;letter-spacing:.4px}
.card-info b{font-weight:700}
.pin{display:inline-block;width:8px;height:10px;vertical-align:-1px;margin-right:3px}

/* sidebar */
.widget{left:513px;width:216px;background:#e7e7e7;border:2px solid #d6d6d6}
.widget h2{font-family:"Open Sans",sans-serif;font-weight:600;font-size:16px;color:#333;letter-spacing:.3px}
.featured{top:467px;height:267px;text-align:center}
.featured h2{text-align:left;padding:19px 0 0 15px}
.featured .cap{font-size:8.5px;font-weight:700;line-height:13px;margin-top:14px}
.featured .pic{margin:12px auto 0;width:132px;height:80px;border:2px solid #e63347;background:linear-gradient(#a9c3d9,#c8d0d2 40%,#6d8453 70%,#4f6b3a)}
.featured .addr{font-size:8.5px;line-height:12px;margin-top:16px}
.news{top:765px;height:212px;padding:18px 0 0 12px}
.news ul{list-style:none;margin-top:12px}
.news li{font-size:9.5px;color:#333;line-height:11.5px;margin-bottom:8px;width:190px}
.testi{top:1010px;height:213px;padding:20px 14px 0 12px}
.testi blockquote{font-style:italic;font-size:9.5px;line-height:15px;color:#333;margin-top:12px;padding-left:4px}
.testi .who{color:var(--red);font-style:italic;font-weight:700;font-size:10px;margin:12px 0 0 4px}

/* footer */
.footer{left:0;top:1342px;width:740px;height:128px;background:var(--footer)}
.contact{left:14px;top:30px;color:#fff;font-size:10px;line-height:18px}
.foot-brand{left:309px;top:24px;width:166px;height:76px;border-radius:50%;background:#4a4a4a;border:2px solid #8a8a8a;display:flex;align-items:center;justify-content:center}
.foot-brand span{font-family:"Open Sans",sans-serif;font-weight:700;font-size:15px;color:#eee}
.badges{left:508px;top:18px;width:210px}
.badges span{position:absolute;background:#e4e4e4;display:block}
.copyright{left:0;top:1470px;width:740px;height:30px;background:var(--red);color:#fff;font-size:10px;text-align:center;line-height:27px}
</style>
</head>
<body>
<div class="stage">
<div class="page">

  <header>
    <div class="abs brand"><span class="brand-dot"></span><span class="brand-name">Dorrel Commercial</span></div>
    <div class="abs tagline">Our Signs are Everywhere</div>
    <div class="abs social" aria-label="Social media links"><span></span><span></span><span></span><span></span><span></span></div>
  </header>

  <nav class="abs nav">
    <a href="#" style="width:64px">HOME</a>
    <a href="#" style="width:144px">PROPERTIES FOR SALE</a>
    <a href="#" class="active" style="width:87px">AUCTIONS</a>
    <a href="#" style="width:142px">SELL YOUR PROPERTY</a>
    <a href="#" style="width:119px">COMMUNITY INFO</a>
    <a href="#" style="width:89px">ABOUT US</a>
    <a href="#" style="width:95px;border-right:0">CONTACT US</a>
  </nav>

  <div class="abs hero" role="img" aria-label="Slideshow photo: red-sided family home with stone accents and landscaped front yard"></div>

  <div class="abs dropdown">
    <a href="#" class="up">Upcoming Auction</a>
    <a href="#" class="past">Past Auction</a>
  </div>

  <section class="abs welcome">
    <h1>Welcome To Dorrel Commercial Realtors, Auctioneers LLC</h1>
    <p>With over 30 years experience, Dorrel Commercial Realtors, Auctioneers LLC is one of the leading real estate companies in Middle TN. Specializing in commercial, residential and auctions, we can service all of your real estate needs.</p>
  </section>

  <!-- auction listings -->
  <article class="abs card" style="top:561px">
    <div class="card-head">ART, FURNITURE AND ACCESSORIES ONLINE AUCTION</div>
    <div class="abs card-photo" role="img" aria-label="Open farmland tract under a pale sky"></div>
    <div class="abs card-btn" style="top:138px"><i></i>Details</div>
    <div class="abs card-btn" style="top:171px"><i></i>Photos</div>
    <div class="abs card-date">THURSDAY, AUGUST 21ST AT 10:00 A.M.</div>
    <div class="abs card-desc">Selling 3120 Acres of land in tracts of 2590 Acres &amp; 560 Acres</div>
    <div class="abs bid"><svg width="13" height="12" viewBox="0 0 13 12"><rect x="1" y="1" width="11" height="7" fill="none" stroke="#222" stroke-width="1.4"/><rect x="4" y="9.5" width="5" height="1.5" fill="#222"/></svg>Click Here to Bid Online Now!</div>
    <div class="abs card-info">
      <b>LIVE OFF-SITE AUCTION</b><br><b>Auction Location:</b><br>
      <svg class="pin" viewBox="0 0 8 10"><path d="M4 10 L0.8 5 A3.4 3.4 0 1 1 7.2 5 Z" fill="#d10f1c"/></svg>418 N Mesa Road, Calder, OK 73990<br>
      <b>Property Location:</b><br>
      <svg class="pin" viewBox="0 0 8 10"><path d="M4 10 L0.8 5 A3.4 3.4 0 1 1 7.2 5 Z" fill="#d10f1c"/></svg>418 N Mesa Road, Calder, OK 73990<br>
      <span style="padding-left:35px">08/21/14 at 10:00 AM CDT</span>
    </div>
  </article>

  <article class="abs card" style="top:824px">
    <div class="card-head">ART, FURNITURE AND ACCESSORIES ONLINE AUCTION</div>
    <div class="abs card-photo" role="img" aria-label="Open farmland tract under a pale sky"></div>
    <div class="abs card-btn" style="top:138px"><i></i>Details</div>
    <div class="abs card-btn" style="top:171px"><i></i>Photos</div>
    <div class="abs card-date">THURSDAY, AUGUST 21ST AT 10:00 A.M.</div>
    <div class="abs card-desc">Selling 3120 Acres of land in tracts of 2590 Acres &amp; 560 Acres</div>
    <div class="abs bid"><svg width="13" height="12" viewBox="0 0 13 12"><rect x="1" y="1" width="11" height="7" fill="none" stroke="#222" stroke-width="1.4"/><rect x="4" y="9.5" width="5" height="1.5" fill="#222"/></svg>Click Here to Bid Online Now!</div>
    <div class="abs card-info">
      <b>LIVE OFF-SITE AUCTION</b><br><b>Auction Location:</b><br>
      <svg class="pin" viewBox="0 0 8 10"><path d="M4 10 L0.8 5 A3.4 3.4 0 1 1 7.2 5 Z" fill="#d10f1c"/></svg>418 N Mesa Road, Calder, OK 73990<br>
      <b>Property Location:</b><br>
      <svg class="pin" viewBox="0 0 8 10"><path d="M4 10 L0.8 5 A3.4 3.4 0 1 1 7.2 5 Z" fill="#d10f1c"/></svg>418 N Mesa Road, Calder, OK 73990<br>
      <span style="padding-left:35px">08/21/14 at 10:00 AM CDT</span>
    </div>
  </article>

  <article class="abs card" style="top:1085px;left:17px">
    <div class="card-head">ART, FURNITURE AND ACCESSORIES ONLINE AUCTION</div>
    <div class="abs card-photo" role="img" aria-label="Open farmland tract under a pale sky"></div>
    <div class="abs card-btn" style="top:138px"><i></i>Details</div>
    <div class="abs card-btn" style="top:171px"><i></i>Photos</div>
    <div class="abs card-date">THURSDAY, AUGUST 21ST AT 10:00 A.M.</div>
    <div class="abs card-desc">Selling 3120 Acres of land in tracts of 2590 Acres &amp; 560 Acres</div>
    <div class="abs bid"><svg width="13" height="12" viewBox="0 0 13 12"><rect x="1" y="1" width="11" height="7" fill="none" stroke="#222" stroke-width="1.4"/><rect x="4" y="9.5" width="5" height="1.5" fill="#222"/></svg>Click Here to Bid Online Now!</div>
    <div class="abs card-info">
      <b>LIVE OFF-SITE AUCTION</b><br><b>Auction Location:</b><br>
      <svg class="pin" viewBox="0 0 8 10"><path d="M4 10 L0.8 5 A3.4 3.4 0 1 1 7.2 5 Z" fill="#d10f1c"/></svg>418 N Mesa Road, Calder, OK 73990<br>
      <b>Property Location:</b><br>
      <svg class="pin" viewBox="0 0 8 10"><path d="M4 10 L0.8 5 A3.4 3.4 0 1 1 7.2 5 Z" fill="#d10f1c"/></svg>418 N Mesa Road, Calder, OK 73990<br>
      <span style="padding-left:35px">08/21/14 at 10:00 AM CDT</span>
    </div>
  </article>

  <!-- sidebar -->
  <aside>
    <section class="abs widget featured">
      <h2>Featured Property</h2>
      <div class="cap">13.35 ACRES OF PRIME DEVELOP<br>&amp; 33RD STREET</div>
      <div class="pic" role="img" aria-label="Two-story house with a crowd gathered on the lawn"></div>
      <div class="addr">LOTS 13 &amp; 14 FOR SALE, BRAMFIELD<br>IOWA<br>Third Street, Bramfield, IA 52699</div>
    </section>

    <section class="abs widget news">
      <h2>News &amp; Events blog</h2>
      <ul>
        <li>Great Land Auction Companies Make All the Difference</li>
        <li>Great OK Farms for Sale at Auction Prices</li>
        <li>Farmland Auctions on Route 66</li>
        <li>Great Land Auction Companies Make All the Difference</li>
        <li>Great OK Farms for Sale at Auction Prices</li>
      </ul>
    </section>

    <section class="abs widget testi">
      <h2>Testimonials</h2>
      <blockquote>“ It is a long established fact that a reader will be distracted by the readable content of a page when looking at its layout. The point of using Lorem Ipsum is that it has a more-or-less normal distribution of letters, as opposed to using. ”</blockquote>
      <div class="who">Harlan Mercer</div>
    </section>
  </aside>

  <footer>
    <div class="abs footer">
      <div class="abs contact">
        Phone: (615) 555-0178<br>
        Contacts: Marion Teague-Hollis<br>
        Email: marketing@kenwoodorrel.example<br>
        Address: 22-C Elmfield Court W, Murfreesboro, TN 37199
      </div>
      <div class="abs foot-brand"><span>Dorrel Commercial</span></div>
      <div class="abs badges" aria-label="Association memberships">
        <span style="left:12px;top:0;width:44px;height:38px;border-radius:4px"></span>
        <span style="left:72px;top:4px;width:42px;height:30px"></span>
        <span style="left:124px;top:6px;width:30px;height:28px;transform:rotate(45deg) scale(.75)"></span>
        <span style="left:166px;top:2px;width:32px;height:32px;border-radius:50% 50% 50% 50%/40% 40% 60% 60%"></span>
        <span style="left:0;top:62px;width:46px;height:20px;border-radius:50%"></span>
        <span style="left:56px;top:54px;width:34px;height:34px;border-radius:50%"></span>
        <span style="left:100px;top:56px;width:60px;height:30px"></span>
        <span style="left:172px;top:52px;width:34px;height:36px"></span>
      </div>
    </div>
    <div class="abs copyright">Copyright © 2007 - 2014 • Dorrel Commercial Realtors, Auctioneers LLC • All Rights Reserved.</div>
  </footer>

</div>
</div>
</body>
</html>
```